New business card/stationary for a consulting company

I am looking for a clean and very professional looking business card for my consulting company as well as corresponding stationary. I am uploading our logo. I like simple and powerful for the feel. No graphics but I am open on everything else. Below is my contact information but would like the final to be in a version I can add my employees information into and print. Thank you.

Daniel Whitcombe
dan@ferncliffadvisory.com
2870 North 9th Avenue, Summit Floor, Elm Ridge, Illinois 60531
www.ferncliffadvisory.com

Industry/Entity Type

Consulting

Contact Information for Business Card

Daniel Whitcombe
dan@ferncliffadvisory.com
www.ferncliffadvisory.com

Font styles to use
Serif
Sans Serif

Requirements
Must have
• Our logo and the business card details.
Nice to have
• our website www.ferncliffadvisory.com

```html
<!DOCTYPE html>
<html lang="en">
<head>
<meta charset="UTF-8">
<title>Ferncliff Advisory — Business Card</title>
<link rel="stylesheet" href="https://fonts.googleapis.com/css2?family=Tenor+Sans&family=Lato:wght@400;700&display=swap">
<style>
  :root {
    --navy: #08066e;
    --white: #ffffff;
    --ink: #111111;
    --backdrop: #2b2b2b;
    --shadow: rgba(0, 0, 0, 0.45);
  }
  * { box-sizing: border-box; margin: 0; padding: 0; }
  html, body { width: 1200px; height: 900px; overflow: hidden; }
  body {
    background: var(--backdrop);
    position: relative;
    font-family: "Lato", sans-serif;
  }
  .card {
    position: absolute;
    left: 250px;
    width: 700px;
    height: 400px;
    box-shadow: 0 10px 24px var(--shadow);
    overflow: hidden;
  }
  .card--back { top: 36px; background: var(--navy); }
  .card--front { top: 464px; background: var(--white); }

  .wordmark {
    position: absolute;
    left: 0; right: 0;
    display: flex;
    justify-content: center;
    align-items: center;
    gap: 18px;
    font-family: "Tenor Sans", sans-serif;
    font-size: 40px;
    letter-spacing: 3px;
    text-transform: uppercase;
    white-space: nowrap;
  }
  .wordmark__square { width: 22px; height: 22px; display: block; }
  .card--back .wordmark { top: 172px; color: var(--white); }
  .card--back .wordmark__square { background: var(--white); }
  .card--front .wordmark { top: 90px; color: var(--navy); }
  .card--front .wordmark__square { background: var(--navy); }

  .person-name {
    position: absolute;
    top: 196px;
    left: 0; right: 0;
    text-align: center;
    font-size: 31px;
    letter-spacing: 1px;
    color: var(--navy);
    text-transform: uppercase;
  }
  .divider {
    position: absolute;
    top: 246px;
    left: 60px;
    right: 60px;
    height: 2px;
    background: var(--navy);
  }
  .contact-row {
    position: absolute;
    top: 268px;
    left: 0; right: 0;
    display: flex;
    justify-content: center;
    align-items: center;
    gap: 14px;
    font-size: 20px;
    color: var(--ink);
  }
  .contact-item { display: flex; align-items: center; gap: 8px; }
  .contact-item svg { width: 20px; height: 20px; }
  .address {
    position: absolute;
    top: 310px;
    left: 0; right: 0;
    text-align: center;
    font-size: 20px;
    color: var(--ink);
  }
  .base-band {
    position: absolute;
    left: 0; right: 0; bottom: 0;
    height: 14px;
    background: var(--navy);
  }
</style>
</head>
<body>
  <section class="card card--back" aria-label="Card back">
    <div class="wordmark"><span class="wordmark__square"></span>Ferncliff Advisory</div>
  </section>

  <section class="card card--front" aria-label="Card front">
    <div class="wordmark"><span class="wordmark__square"></span>Ferncliff Advisory</div>
    <div class="person-name">Daniel Whitcombe</div>
    <div class="divider"></div>
    <div class="contact-row">
      <span class="contact-item">
        <svg viewBox="0 0 20 20" aria-hidden="true">
          <rect x="2" y="5" width="16" height="11" fill="var(--navy)"/>
          <polyline points="2,5 10,11 18,5" fill="none" stroke="var(--white)" stroke-width="1.4"/>
        </svg>
        dan@ferncliffadvisory.com
      </span>
      <span class="contact-item">
        <svg viewBox="0 0 20 20" aria-hidden="true">
          <circle cx="10" cy="10" r="8" fill="var(--navy)"/>
          <ellipse cx="10" cy="10" rx="3.5" ry="8" fill="none" stroke="var(--white)" stroke-width="1.1"/>
          <line x1="2" y1="10" x2="18" y2="10" stroke="var(--white)" stroke-width="1.1"/>
          <line x1="3.5" y1="6" x2="16.5" y2="6" stroke="var(--white)" stroke-width="1"/>
          <line x1="3.5" y1="14" x2="16.5" y2="14" stroke="var(--white)" stroke-width="1"/>
        </svg>
        www.ferncliffadvisory.com
      </span>
    </div>
    <div class="address">2870 North 9th Avenue, Summit Floor, Elm Ridge, Illinois 60531</div>
    <div class="base-band"></div>
  </section>
</body>
</html>
```